Postcard Design Project A Healthy reminder

Dr.'s Dhelpit and Sirel dunwat. Internal Medicine/Family practice. This postcard will be for our patients that we have not seen in a while. Also we need another postcard (the one your designing) with a different heading for New patient's. Do you offer a price break for that? The only thing we would need to change is the heading. Please let me know. Thank you so much! Also can you use the map on the last postcard and our logo I made? I cant find it. Please feel free to call me or email me.

```html
<!DOCTYPE html>
<html lang="en">
<head>
<meta charset="utf-8">
<title>A Healthy Reminder – Postcard</title>
<link href="https://fonts.googleapis.com/css2?family=Arimo:wght@400;700&family=Source+Serif+4:opsz,wght@8..60,400;8..60,700;8..60,900&display=swap" rel="stylesheet">
<style>
  :root {
    --red: #a50d10;
    --red-dark: #8a0708;
    --ink: #1b1b1b;
    --paper: #ffffff;
    --paper-soft: #f1f1f1;
    --silver: #c4c4c4;
    --backdrop: #e6ecec;
    --map-a: #cfe3c4;
    --map-b: #e4e4e2;
    --green-a: #6f8a4c;
    --green-b: #b9b2a2;
  }
  * { box-sizing: border-box; margin: 0; padding: 0; }
  html, body { width: 1200px; height: 891px; overflow: hidden; }
  body { background: var(--backdrop); position: relative; font-family: "Source Serif 4", Georgia, serif; }

  .card { position: absolute; background: var(--paper); box-shadow: 0 6px 18px rgba(0,0,0,.18); overflow: hidden; }
  .card > svg { position: absolute; inset: 0; z-index: 0; }
  .card > div, .card > h2, .card > p { z-index: 1; }

  /* Front */
  .card-front { left: 520px; top: 24px; width: 640px; height: 420px; }
  .logo { position: absolute; left: 30px; top: 34px; width: 250px; text-align: center; }
  .logo-row { display: flex; align-items: center; justify-content: center; gap: 8px; }
  .logo-mark { width: 14px; height: 14px; background: var(--red); }
  .logo-name { font-family: "Arimo", Arial, sans-serif; font-weight: 700; font-size: 15px; color: var(--ink); }
  .logo-tag { font-family: "Arimo", Arial, sans-serif; font-size: 7px; font-weight: 700; letter-spacing: .6px; color: #333; margin-top: 6px; }

  .headline { position: absolute; left: 44px; top: 100px; color: var(--ink); line-height: 1; }
  .headline .lead { font-size: 21px; transform: scaleX(.88); transform-origin: left; white-space: nowrap; }
  .headline .lead strong { color: var(--red); font-weight: 700; }
  .headline .lead + .lead { margin-top: 5px; }
  .headline .big { font-weight: 900; font-size: 56px; line-height: .95; letter-spacing: 1px; margin-top: 2px; }
  .headline .big.red { color: var(--red); margin-top: -4px; }

  .contact { position: absolute; left: 40px; top: 306px; color: #fff; }
  .contact .addr { font-size: 14px; line-height: 1.2; display: flex; gap: 6px; }
  .contact .phone { font-size: 28px; font-weight: 700; margin-top: 6px; display: flex; align-items: center; gap: 8px; }
  .contact .web { font-size: 14px; margin-top: 2px; display: flex; align-items: center; gap: 6px; }

  /* Back */
  .card-back { left: 40px; top: 460px; width: 640px; height: 412px; }
  .back-title { position: absolute; left: 26px; top: 14px; color: var(--red); font-weight: 900; font-style: italic; font-size: 19px; line-height: 1.05; }
  .back-title span { color: var(--ink); font-weight: 400; }
  .call-now { position: absolute; left: 40px; top: 196px; color: #fff; font-weight: 700; font-size: 24px; line-height: 1.05; letter-spacing: 1px; }
  .back-info { position: absolute; left: 20px; top: 272px; color: var(--ink); font-size: 11px; line-height: 1.35; }
  .back-info .social { display: flex; align-items: center; gap: 5px; font-weight: 700; font-size: 9px; letter-spacing: .5px; }
  .back-info .social i { width: 10px; height: 10px; border-radius: 50%; background: #3b5a98; display: inline-block; }
  .back-info .url { font-style: italic; }
  .back-info .url b { color: var(--red); }
  .back-info .loc { font-size: 13px; margin-top: 4px; }
  .back-info .loc strong { display: block; font-weight: 900; }
</style>
</head>
<body>

<section class="card card-front" aria-label="Postcard front">
  <svg viewBox="0 0 640 420" width="640" height="420">
    <defs>
      <linearGradient id="frontPaper" x1="0" y1="0" x2="0" y2="1">
        <stop offset="0" stop-color="#ffffff"/><stop offset="1" stop-color="#ececec"/>
      </linearGradient>
      <linearGradient id="hallPhoto" x1="0" y1="0" x2="1" y2="1">
        <stop offset="0" stop-color="#e8dccb"/><stop offset=".55" stop-color="#d9c7b0"/><stop offset="1" stop-color="#9a9c9f"/>
      </linearGradient>
    </defs>
    <rect width="640" height="420" fill="url(#frontPaper)"/>
    <path d="M0 290 Q150 262 330 296 L330 420 L0 420 Z" fill="var(--red)"/>
    <path d="M344 0 C262 120 236 300 332 420 L300 420 C206 300 234 118 318 0 Z" fill="var(--red)"/>
    <path d="M354 0 C274 120 248 300 346 420 L334 420 C238 300 264 118 342 0 Z" fill="var(--silver)"/>
    <path role="img" aria-label="Photo: two doctors in white coats reviewing charts in a clinic hallway" d="M362 0 C282 120 256 300 354 420 L640 420 L640 0 Z" fill="url(#hallPhoto)"/>
  </svg>

  <div class="logo">
    <div class="logo-row"><span class="logo-mark"></span><span class="logo-name">Dhelpit T. Dunwat, M.D.</span></div>
    <div class="logo-tag">A Primary Care Office</div>
  </div>

  <div class="headline">
    <p class="lead">A healthy <strong>reminder,</strong></p>
    <p class="lead">It is time for your</p>
    <p class="big">annual</p>
    <p class="big red">exam.</p>
  </div>

  <div class="contact">
    <p class="addr">
      <svg width="10" height="14" viewBox="0 0 10 14"><path d="M5 1a3.5 3.5 0 0 1 3.5 3.5C8.5 7 5 11 5 11S1.5 7 1.5 4.5A3.5 3.5 0 0 1 5 1z" fill="none" stroke="#fff" stroke-width="1.3"/><line x1="1" y1="13" x2="9" y2="13" stroke="#fff" stroke-width="1.3"/></svg>
      <span>4820 N. Marlow Street Suite 214<br>Halden, Ca 93811</span>
    </p>
    <p class="phone">
      <svg width="22" height="22" viewBox="0 0 22 22"><circle cx="11" cy="11" r="9.5" fill="none" stroke="#fff" stroke-width="1.6"/><path d="M8 6.5l2 2-1.2 1.5a7 7 0 0 0 3.2 3.2l1.5-1.2 2 2-1.4 1.6c-3.6-.6-6.8-3.8-7.4-7.4z" fill="#fff"/></svg>
      (555) 014-2290
    </p>
    <p class="web">
      <svg width="11" height="11" viewBox="0 0 12 12"><circle cx="6" cy="6" r="5" fill="none" stroke="#fff"/><ellipse cx="6" cy="6" rx="2.2" ry="5" fill="none" stroke="#fff"/><line x1="1" y1="6" x2="11" y2="6" stroke="#fff"/></svg>
      www.dhelpitdunwatmd.com
    </p>
  </div>
</section>

<section class="card card-back" aria-label="Postcard back">
  <svg viewBox="0 0 640 412" width="640" height="412">
    <defs>
      <linearGradient id="mapTone" x1="0" y1="0" x2="1" y2="0">
        <stop offset="0" stop-color="var(--map-a)"/><stop offset="1" stop-color="var(--map-b)"/>
      </linearGradient>
      <linearGradient id="buildingTone" x1="0" y1="0" x2="0" y2="1">
        <stop offset="0" stop-color="var(--green-a)"/><stop offset=".55" stop-color="var(--green-b)"/><stop offset="1" stop-color="#7fa052"/>
      </linearGradient>
    </defs>
    <rect width="640" height="412" fill="var(--paper)"/>
    <path d="M0 0 L320 0 C400 110 392 300 240 412 L0 412 Z" fill="var(--paper-soft)"/>
    <path d="M320 0 C400 110 392 300 240 412 L262 412 C414 300 424 110 346 0 Z" fill="var(--red)"/>
    <path d="M346 0 C424 110 414 300 262 412 L270 412 C422 300 432 110 356 0 Z" fill="var(--silver)"/>
    <path role="img" aria-label="Street map showing the clinic location" d="M0 58 L352 58 C368 100 376 140 378 178 L0 178 Z" fill="url(#mapTone)"/>
    <path d="M0 186 L390 186 L390 252 L0 262 Z" fill="var(--red)"/>
    <circle cx="332" cy="224" r="58" fill="var(--red-dark)"/>
    <circle role="img" aria-label="Photo of the clinic entrance with garden" cx="332" cy="224" r="52" fill="url(#buildingTone)"/>
    <rect x="506" y="34" width="96" height="62" fill="none" stroke="#444" stroke-width="1.2"/>
    <line x1="440" y1="170" x2="610" y2="170" stroke="#333"/>
    <line x1="440" y1="205" x2="610" y2="205" stroke="#333"/>
    <line x1="440" y1="240" x2="610" y2="240" stroke="#333"/>
  </svg>

  <h2 class="back-title">Dr.'s Dhelpit <span>and</span><br>Sirel Dunwat</h2>
  <p class="call-now">CALL NOW<br>(555) 014-2290</p>
  <div class="back-info">
    <p class="social">VISIT US ON <i></i> Linkboard</p>
    <p class="url">www.linkboard.com/<b>doctorsdunwat</b></p>
    <p class="loc">Located On The<strong>SE corner of Marlow and Tarrow.</strong></p>
  </div>
</section>

</body>
</html>
```